Client Meeting and installation Email Follow up

I would like a follow-up email template created.
Currently, we do a lot of new construction builds and meet with clients about 6-3 months before they take possession of their new house. I want a follow-up email template to be sent after the homeowner takes possession of their house that enquires if the clients are happy about their new lighting, the service they received, and their customer service representative with Brightwell Lamps and Breezes. I have attached a few files of what our current marketing looks like.
Target Market(s)
Home Owners We have already met with
Industry/Entity Type
Residential lighting
Font styles to use
Other font styles liked:
- Alta Light, Playfair Display, Montserrat
Colors
Designer to choose colors to be used in the design.
Look and feel
Each slider illustrates characteristics of the customer's brand and the style your logo design should communicate.

```html
<!DOCTYPE html>
<html lang="en">
<head>
<meta charset="utf-8">
<title>Brightwell Lamps and Breezes – Follow Up</title>
<link rel="stylesheet" href="https://fonts.googleapis.com/css2?family=Fira+Sans+Condensed:wght@500;600&family=Roboto:wght@400;500;600&display=swap">
<style>
  :root {
    --ink: #000000;
    --paper: #ffffff;
    --body-text: #1a1a1a;
    --footer-bg: #f2f2f2;
    --frame-grey: #ebebeb;
    --band-dark: #0b0d10;
    --shadow-dark: #25272b;
  }
  * { margin: 0; padding: 0; box-sizing: border-box; }
  html, body { width: 1200px; height: 2902px; overflow: hidden; background: var(--paper); }
  body { position: relative; font-family: "Roboto", Arial, sans-serif; color: var(--body-text); }
  .abs { position: absolute; }

  .brand {
    left: 0; width: 1200px; text-align: center;
    font-family: "Fira Sans Condensed", Arial, sans-serif; font-weight: 600;
    color: var(--ink); letter-spacing: 1px; text-transform: uppercase;
  }
  .brand-top { top: 22px; font-size: 34px; line-height: 1.1; }
  .brand-top small, .brand-foot small { display: block; font-size: 0.55em; letter-spacing: 3px; }
  .brand-foot { top: 2584px; font-size: 46px; line-height: 1.1; }

  .hero {
    left: 60px; top: 97px; width: 1080px; height: 525px; border-radius: 27px; overflow: hidden;
    background: linear-gradient(100deg, #3a3835 0%, #4a4742 45%, #6a6d62 75%, #8d9a84 100%);
  }
  .hero-title {
    left: 0; width: 1200px; top: 288px; text-align: center; color: var(--paper);
    font-family: "Fira Sans Condensed", Arial, sans-serif; font-weight: 600;
    font-size: 54px; line-height: 69px; text-shadow: 0 2px 6px rgba(0,0,0,.4);
  }

  .section-title {
    font-family: "Fira Sans Condensed", Arial, sans-serif; font-weight: 600; font-size: 36px; line-height: 1.2;
  }
  .intro-title { left: 62px; top: 738px; color: var(--ink); }
  .bullets { list-style: none; font-size: 20px; line-height: 40px; }
  .bullets li { position: relative; padding-left: 30px; }
  .bullets li::before {
    content: ""; position: absolute; left: 0; top: 14px; width: 14px; height: 14px; border-radius: 50%;
    background: currentColor;
  }
  .intro-list { left: 60px; top: 806px; width: 520px; color: var(--body-text); }
  .intro-list li + li { margin-top: 41px; }

  .btn {
    display: flex; align-items: center; justify-content: center;
    font-family: "Roboto", Arial, sans-serif; font-weight: 500; font-size: 20px; text-decoration: none;
  }
  .btn-dark { background: var(--ink); color: var(--paper); }
  .btn-light { background: var(--paper); color: var(--ink); }
  .learn-btn { left: 60px; top: 1041px; width: 165px; height: 60px; }

  .photo-frame { left: 620px; top: 699px; width: 490px; height: 423px; background: var(--frame-grey); }
  .hallway-photo { left: 652px; top: 727px; width: 485px; height: 419px;
    background: linear-gradient(90deg, #d9d6d1 0%, #f1efec 35%, #b9c2ae 55%, #eceae6 70%, #bcc9cf 100%); }

  .experience-band { left: 0; top: 1242px; width: 1200px; height: 550px;
    background: linear-gradient(135deg, #14171c 0%, var(--band-dark) 50%, #181b20 100%); }
  .kitchen-shadow { left: 84px; top: 1357px; width: 495px; height: 360px; background: var(--shadow-dark); border-radius: 12px; }
  .kitchen-photo { left: 60px; top: 1330px; width: 495px; height: 360px; border-radius: 12px;
    background: linear-gradient(160deg, #e6e4e0 0%, #cfcac3 40%, #a9a39b 70%, #dedad4 100%); }
  .experience-title { left: 651px; top: 1336px; color: var(--paper); }
  .experience-list { left: 653px; top: 1396px; width: 400px; color: var(--paper); font-size: 20px; line-height: 44px; }
  .experience-list li::before { top: 15px; }
  .feedback-btn-light { left: 652px; top: 1632px; width: 204px; height: 60px; }

  .closing-note { left: 0; width: 1200px; top: 1866px; text-align: center;
    font-size: 30px; font-weight: 500; line-height: 45px; color: var(--ink); }
  .feedback-btn-dark { left: 490px; top: 1978px; width: 221px; height: 60px; }

  .gallery-photo { top: 2092px; width: 345px; height: 314px; border-radius: 6px; }
  .gallery-living { left: 60px; background: linear-gradient(180deg, #5f7a4a 0%, #7f9768 50%, #3a3430 100%); }
  .gallery-bedroom { left: 429px; background: linear-gradient(180deg, #d8cdc1 0%, #c9bcae 60%, #5b5048 100%); }
  .gallery-bath { left: 795px; background: linear-gradient(180deg, #b7aea6 0%, #d3ccc4 55%, #a48a6c 100%); }

  .site-footer { left: 0; top: 2505px; width: 1200px; height: 397px; background: var(--footer-bg); }
  .contact { top: 2720px; display: flex; align-items: center; gap: 24px; font-size: 18px; line-height: 33px; color: var(--ink); }
  .contact-icon { width: 48px; height: 48px; border-radius: 50%; background: var(--ink);
    display: flex; align-items: center; justify-content: center; flex: none; }
  .contact-address { left: 108px; }
  .contact-phone { left: 508px; }
  .contact-email { left: 828px; }
  .copyright { left: 0; width: 1200px; top: 2828px; text-align: center; font-size: 17px; color: var(--ink); }
</style>
</head>
<body>

  <div class="abs brand brand-top">Brightwell<small>Lamps &amp; Breezes</small></div>

  <div class="abs hero" role="img" aria-label="Dimly lit home office with built-in shelving, a wooden desk and a tall window"></div>
  <h1 class="abs hero-title">Welcome to Your Bright New<br>Beginning!</h1>

  <h2 class="abs section-title intro-title">How Do You Like It ?</h2>
  <ul class="abs bullets intro-list">
    <li>We hope you're enjoying your new home and its stunning lighting from Brightwell Lamps and Breezes.</li>
    <li>Now that you've had time to settle in, we'd love to hear your thoughts.</li>
  </ul>
  <a class="abs btn btn-dark learn-btn" href="#">Learn More</a>

  <div class="abs photo-frame"></div>
  <div class="abs hallway-photo" role="img" aria-label="Bright entry hallway with a pendant light, gallery wall and glass doors to a garden"></div>

  <section class="abs experience-band"></section>
  <div class="abs kitchen-shadow"></div>
  <div class="abs kitchen-photo" role="img" aria-label="Open kitchen with marble island, range and pendant lights leading to a living area"></div>
  <h2 class="abs section-title experience-title">Tell us about your experience</h2>
  <ul class="abs bullets experience-list">
    <li>Are you satisfied with the lighting installation?</li>
    <li>How was the service you received?"</li>
    <li>How did your customer service representative do?</li>
  </ul>
  <a class="abs btn btn-light feedback-btn-light" href="#">Provide Feedback</a>

  <p class="abs closing-note">Your feedback helps us to serve you better. Please don’t hesitate to share<br>your thoughts or get in touch if you have any questions.</p>
  <a class="abs btn btn-dark feedback-btn-dark" href="#">Provide Feedback</a>

  <div class="abs gallery-photo gallery-living" role="img" aria-label="Living room with a ring chandelier in front of tall windows onto trees"></div>
  <div class="abs gallery-photo gallery-bedroom" role="img" aria-label="Neutral bedroom with a slim wall sconce above the bed"></div>
  <div class="abs gallery-photo gallery-bath" role="img" aria-label="Bathroom with a round backlit mirror and twin vessel sinks"></div>

  <footer class="abs site-footer"></footer>
  <div class="abs brand brand-foot">Brightwell<small>Lamps &amp; Breezes</small></div>

  <div class="abs contact contact-address">
    <span class="contact-icon">
      <svg width="22" height="22" viewBox="0 0 24 24"><path d="M12 2a7 7 0 0 0-7 7c0 5 7 13 7 13s7-8 7-13a7 7 0 0 0-7-7zm0 9.5A2.5 2.5 0 1 1 12 6.5a2.5 2.5 0 0 1 0 5z" fill="#fff"/></svg>
    </span>
    <span>1270 Lantern Row S.E<br>Calgary, AB T2X 4K1 CA</span>
  </div>
  <div class="abs contact contact-phone">
    <span class="contact-icon">
      <svg width="22" height="22" viewBox="0 0 24 24"><path d="M6.6 10.8a15.1 15.1 0 0 0 6.6 6.6l2.2-2.2a1 1 0 0 1 1-.25 11.4 11.4 0 0 0 3.6.57 1 1 0 0 1 1 1V20a1 1 0 0 1-1 1A17 17 0 0 1 3 4a1 1 0 0 1 1-1h3.5a1 1 0 0 1 1 1c0 1.25.2 2.45.57 3.57a1 1 0 0 1-.25 1z" fill="#fff"/></svg>
    </span>
    <span>403.555.0187</span>
  </div>
  <div class="abs contact contact-email">
    <span class="contact-icon">
      <svg width="20" height="20" viewBox="0 0 24 24"><path d="M3 5h18a1 1 0 0 1 1 1v12a1 1 0 0 1-1 1H3a1 1 0 0 1-1-1V6a1 1 0 0 1 1-1zm9 7.5L20 7H4z" fill="#fff"/></svg>
    </span>
    <span>hello@brightwelllamps.com</span>
  </div>

  <p class="abs copyright">Copyrights@2024.Brightwell.All Rights Reserved</p>

</body>
</html>
```